Belmont Ridge Business Card Design Project

We have recently rebranded and would like to design new business cards that incorporate the corporate logo - double sided cards with corporate logo on one side and contact details on the other

Target Market(s)

Sophisticated and high net worth investors and finance industry professionals

Industry/Entity Type

Funds Management

Contact Information for Business Card

The card should prominently feature the company name and logo. Other details will be standard contact details for each staff member - name, address, phone, email, website

Colors
0054AA
0677BA
7BADD7
CADEEF
E8F1F8

Requirements
Must have
• Double-sided design with one side prominently featuring the corporate logo and the other side with all standard contact details

```html
<!DOCTYPE html>
<html lang="en">
<head>
<meta charset="utf-8">
<title>Belmont Ridge Business Card</title>
<link href="https://fonts.googleapis.com/css2?family=Open+Sans:wght@400;700&display=swap" rel="stylesheet">
<style>
  :root {
    --stage: #ababab;
    --ink-light: #ffffff;
    --night-top: #2c3a52;
    --night-mid: #1c2535;
    --night-low: #0d1117;
    --dusk-top: #8f8a8a;
    --dusk-mid: #d9a27a;
    --dusk-glow: #f5b066;
    --dusk-low: #c9682e;
    --water: #2a2424;
    --card-shadow: rgba(0, 0, 0, 0.45);
  }
  * { margin: 0; padding: 0; box-sizing: border-box; }
  html, body {
    width: 1200px;
    height: 1000px;
    overflow: hidden;
    background: var(--stage);
    font-family: "Open Sans", Arial, sans-serif;
  }
  .canvas {
    position: relative;
    width: 1200px;
    height: 1000px;
  }
  .card {
    position: absolute;
    width: 514px;
    height: 297px;
    overflow: hidden;
    box-shadow: 0 22px 45px var(--card-shadow);
    color: var(--ink-light);
  }
  .card--front { left: 57px; top: 339px; }
  .card--back  { left: 614px; top: 338px; }

  .card__photo {
    position: absolute;
    inset: 0;
  }
  .card--front .card__photo {
    background:
      radial-gradient(ellipse at 50% 20%, rgba(70, 90, 120, 0.55), transparent 60%),
      linear-gradient(180deg, var(--night-top) 0%, var(--night-mid) 55%, var(--night-low) 100%);
  }
  .card--back .card__photo {
    background:
      radial-gradient(ellipse at 52% 92%, rgba(255, 215, 120, 0.9), transparent 45%),
      linear-gradient(180deg, var(--dusk-top) 0%, var(--dusk-mid) 45%, var(--dusk-glow) 75%, var(--dusk-low) 92%, var(--water) 100%);
  }

  .brand-name {
    position: absolute;
    left: 0;
    right: 0;
    top: 143px;
    text-align: center;
    font-weight: 700;
    font-size: 38px;
    letter-spacing: 1px;
    line-height: 1;
  }
  .website {
    position: absolute;
    left: 0;
    right: 0;
    top: 233px;
    text-align: center;
    font-weight: 700;
    font-size: 14px;
  }

  .contact {
    position: absolute;
    left: 43px;
    top: 74px;
    font-size: 14px;
    line-height: 17px;
  }
  .contact__name,
  .contact__role {
    font-weight: 700;
    letter-spacing: 1.3px;
    text-transform: uppercase;
  }
  .contact__lines { margin-top: 15px; }
  .contact__address { margin-top: 17px; }
</style>
</head>
<body>
<main class="canvas">
  <section class="card card--front">
    <div class="card__photo" role="img" aria-label="Looking up between dark glass skyscrapers at dusk"></div>
    <div class="brand-name">Belmont Ridge</div>
    <div class="website">www.belmont-ridge.com</div>
  </section>

  <section class="card card--back">
    <div class="card__photo" role="img" aria-label="Harbour skyline at sunset with a sail-roofed landmark and a bird in the sky"></div>
    <div class="contact">
      <div class="contact__name">Daniel Hartley</div>
      <div class="contact__role">Portfolio Manager</div>
      <div class="contact__lines">
        <div class="contact__phone">+02 9000 4417</div>
        <div class="contact__email">marketneutral@belmont-ridge.com</div>
      </div>
      <div class="contact__address">
        Level 14 Harbour House,<br>
        40 Kent Lane,<br>
        Sydney NSW 2000
      </div>
    </div>
  </section>
</main>
</body>
</html>
```